Simple and Clean business card design

We would like the design to be simple clean and to incorporate our colors.

We are open to your design and talent, we have the dots in our logo as we think of it as data points and we connect data points for people.

We are open to see the great creative and clean design you bring to the table

Contact Information for Business Card

please include: name, position, email, phone and website

Font styles to use
Sans Serif

Requirements
Must have
• my colors incorporated, simplicity
Nice to have
• lots of white space, simplicity
Should not have
• complexicity/ complex art

```html
<!DOCTYPE html>
<html lang="en">
<head>
<meta charset="utf-8">
<title>Kestrel business card</title>
<link href="https://fonts.googleapis.com/css2?family=Lato:wght@400;700;900&display=swap" rel="stylesheet">
<style>
  :root {
    --stage: #2a2624;
    --card: #000000;
    --ink: #ffffff;
    --rule: #5a5a5a;
    --blue: #4285f4;
    --green: #34a853;
    --yellow: #fbbc05;
    --red: #ea4335;
  }
  * { box-sizing: border-box; margin: 0; padding: 0; }
  html, body {
    width: 1200px; height: 842px; overflow: hidden;
    background: var(--stage);
    font-family: "Lato", Arial, sans-serif;
    color: var(--ink);
  }
  .sheet {
    position: relative; width: 1200px; height: 842px;
    display: flex; align-items: center; justify-content: center; gap: 60px;
  }
  .card {
    position: relative; width: 520px; height: 297px;
    background: var(--card);
    box-shadow: 0 10px 30px rgba(0,0,0,.5);
    overflow: hidden;
  }

  /* Contact side */
  .card--contact::before,
  .card--contact::after {
    content: ""; position: absolute; left: 0; right: 0; height: 14px;
    background: var(--blue);
  }
  .card--contact::before { top: 0; }
  .card--contact::after { bottom: 0; }
  .contact {
    position: absolute; inset: 0;
    display: flex; flex-direction: column; align-items: center; justify-content: center;
    text-align: center;
  }
  .contact__name {
    font-weight: 900; font-size: 25px; letter-spacing: .5px; line-height: 1;
  }
  .contact__role {
    font-weight: 400; font-size: 15px; letter-spacing: .5px; margin-top: 3px;
  }
  .contact__icons {
    display: flex; align-items: center; gap: 6px; margin: 10px 0 8px;
  }
  .contact__rule { width: 70px; height: 1px; background: var(--rule); margin: 0 6px; }
  .icon { width: 30px; height: 30px; border-radius: 50%; display: flex; align-items: center; justify-content: center; }
  .icon svg { width: 16px; height: 16px; }
  .icon--phone { background: var(--green); }
  .icon--mail { background: var(--yellow); }
  .icon--web { background: var(--red); }
  .contact__line { font-size: 15px; line-height: 1.3; letter-spacing: .3px; }

  /* Brand side */
  .brand {
    position: absolute; inset: 0;
    display: flex; align-items: center; justify-content: center; gap: 12px;
  }
  .brand__dot { width: 22px; height: 22px; border-radius: 50%; background: var(--blue); }
  .brand__name { font-weight: 900; font-size: 58px; letter-spacing: 1px; color: var(--ink); }
</style>
</head>
<body>
<main class="sheet">
  <section class="card card--contact" aria-label="Contact side">
    <div class="contact">
      <h1 class="contact__name">DANA MORROW</h1>
      <p class="contact__role">Founder/ CEO</p>
      <div class="contact__icons">
        <span class="contact__rule"></span>
        <span class="icon icon--phone">
          <svg viewBox="0 0 24 24" fill="#fff"><path d="M6.6 10.8a15.1 15.1 0 0 0 6.6 6.6l2.2-2.2a1 1 0 0 1 1-.25 11.4 11.4 0 0 0 3.6.57 1 1 0 0 1 1 1V20a1 1 0 0 1-1 1A17 17 0 0 1 3 4a1 1 0 0 1 1-1h3.5a1 1 0 0 1 1 1c0 1.250.2 2.45.57 3.57a1 1 0 0 1-.25 1z"/></svg>
        </span>
        <span class="icon icon--mail">
          <svg viewBox="0 0 24 24" fill="none" stroke="#fff" stroke-width="2"><rect x="3" y="6" width="18" height="12" rx="1"/><path d="M3 7l9 6 9-6"/></svg>
        </span>
        <span class="icon icon--web">
          <svg viewBox="0 0 24 24" fill="none" stroke="#fff" stroke-width="1.6"><circle cx="12" cy="12" r="9"/><ellipse cx="12" cy="12" rx="4" ry="9"/><path d="M3 12h18M4.5 7.5h15M4.5 16.5h15"/></svg>
        </span>
        <span class="contact__rule"></span>
      </div>
      <p class="contact__line">555-201-3847</p>
      <p class="contact__line">dana.morrow@kestrel.one</p>
      <p class="contact__line">www.kestrel.one</p>
    </div>
  </section>

  <section class="card card--brand" aria-label="Brand side">
    <div class="brand">
      <span class="brand__dot"></span>
      <span class="brand__name">Kestrel</span>
    </div>
  </section>
</main>
</body>
</html>
```